Brightway Haul & Upkeep Services, are a company that offers a 'one stop shop' pre-move clean up a

I have already selected a logo which I would like on the front of the business cards along with phone numbers, web address and email which are:
0487650392
www.brightwayhaul.com.au
brightwayhaulandupkeep@mailbox.example

On the back of the card I would like to list some of the types of service we offer (clean - move - repairs/maintenance) which are:
CLEAN - windows, gutters, solar panels, driveways/paths, carpets.
MOVE - Small/medium size house/office moves, large item pick-up & delivery, yard clean-up and removal.
General maintenance and repairs.

I would like the blue logo on a gray background.

Thanks

```html
<!DOCTYPE html>
<html lang="en">
<head>
<meta charset="utf-8">
<title>Brightway Haul & Upkeep Services – Business Card</title>
<link rel="stylesheet" href="https://fonts.googleapis.com/css2?family=Exo+2:wght@400;600;800&display=swap">
<style>
  :root {
    --stage: #2e2e30;
    --card: #ffffff;
    --brand-blue: #1f6fbf;
    --brand-blue-dark: #1a5a9e;
    --light-blue: #6fb3e6;
    --ink: #1c1c1c;
  }
  * { box-sizing: border-box; margin: 0; padding: 0; }
  html, body {
    width: 1200px; height: 900px; overflow: hidden;
    background: var(--stage);
    font-family: "Exo 2", sans-serif;
  }
  .stage { position: relative; width: 1200px; height: 900px; }
  .card {
    position: absolute; left: 290px;
    width: 620px; height: 354px;
    background: var(--card);
    overflow: hidden;
    box-shadow: 0 14px 30px rgba(0,0,0,.45);
  }
  /* Services side */
  .card--services { top: 70px; }
  .services-band { position: absolute; inset: 0; width: 100%; height: 100%; }
  .services-name {
    position: absolute; left: 34px; top: 132px;
    height: 44px; line-height: 44px; white-space: nowrap;
    font-weight: 800; font-size: 34px; letter-spacing: 0.5px;
    color: #ffffff; text-transform: uppercase;
    transform-origin: left bottom;
    transform: rotate(-13.2deg);
  }
  .services-list {
    position: absolute; left: 40px; top: 226px; right: 30px;
    font-size: 14.5px; line-height: 1.5; color: var(--ink);
  }
  .services-list strong { font-weight: 800; }
  .services-list .services-extra { color: var(--light-blue); }

  /* Contact side */
  .card--contact { top: 476px; }
  .contact-footer {
    position: absolute; left: 0; right: 0; bottom: 0; height: 34px;
    background: var(--brand-blue);
    border-top: 8px solid var(--brand-blue-dark);
  }
  .contact-name {
    position: absolute; right: 40px; top: 46px; width: 330px;
    text-align: right;
    font-weight: 800; font-size: 27px; line-height: 1.1;
    color: var(--brand-blue); text-transform: uppercase;
  }
  .contact-list {
    position: absolute; right: 40px; top: 150px;
    list-style: none; text-align: right;
    font-size: 17px; line-height: 1.55; color: var(--ink);
  }
  .contact-list li { display: flex; justify-content: flex-end; align-items: center; gap: 8px; }
  .contact-list .contact-web { color: var(--light-blue); font-size: 18px; }
  .contact-icon { width: 15px; height: 15px; flex: none; }
</style>
</head>
<body>
<main class="stage">

  <section class="card card--services" aria-label="Services side">
    <svg class="services-band" viewBox="0 0 620 354" preserveAspectRatio="none" aria-hidden="true">
      <polygon points="0,0 620,0 620,60 0,205" fill="var(--brand-blue)"/>
    </svg>
    <p class="services-name">Brightway Haul</p>
    <p class="services-list">
      <strong>CLEAN</strong> - windows, gutters, solar panels, driveways/paths, carpets.<br>
      <strong>MOVE</strong> - Small/medium size house/office moves, large item pick-up<br>
      &amp; delivery, yard clean-up and removal.<br>
      <span class="services-extra">General maintenance and repairs.</span>
    </p>
  </section>

  <section class="card card--contact" aria-label="Contact side">
    <p class="contact-name">Brightway Haul &amp; Upkeep Services</p>
    <ul class="contact-list">
      <li>0487650392
        <svg class="contact-icon" viewBox="0 0 16 16" aria-hidden="true"><rect x="4" y="1" width="8" height="14" rx="1.5" fill="var(--brand-blue)"/><rect x="5.5" y="3" width="5" height="8" fill="#fff"/></svg>
      </li>
      <li>brightwayhaulandupkeep@mailbox.example
        <svg class="contact-icon" viewBox="0 0 16 16" aria-hidden="true"><rect x="1" y="3" width="14" height="10" fill="var(--brand-blue)"/><polyline points="1,3 8,9 15,3" fill="none" stroke="#fff" stroke-width="1.4"/></svg>
      </li>
      <li class="contact-web">www.brightwayhaul.com.au
        <svg class="contact-icon" viewBox="0 0 16 16" aria-hidden="true"><circle cx="8" cy="8" r="7" fill="var(--brand-blue)"/><ellipse cx="8" cy="8" rx="3" ry="7" fill="none" stroke="#fff" stroke-width="1"/><line x1="1" y1="8" x2="15" y2="8" stroke="#fff" stroke-width="1"/></svg>
      </li>
    </ul>
    <div class="contact-footer"></div>
  </section>

</main>
</body>
</html>
```